Logo Tweaks & Stationery Design Project for Energy Management Co

We are a specialist metering company trading for over 60 years and have recently developed GPRS metering infrastructure & monitoring services. For more information please see http://www.kestrel-vale.example/remote-meter-reading.html

Due to the success of this system it’s become necessary to open a new company “Brightwell Gauge Ltd” and this project is for relevant stationary designs for our documents.

I need something modern and clear to match our new logo style. Feel free to play around with the colors and tweak the logo if you like.

Maybe with some line chart animation on the header relating to our online services. ( See inspiration file )

Thanks
Derek

Target Market(s)

Renewable Energy Generation Monitoring, Energy Management, Remote Monitoring and Tennant Billing.

Industry/Entity Type

It Company

Requirements
Nice to have
• 100% Carbon neutral hosting
Should not have
• "Clip-Art" should not be used.

```html
<!DOCTYPE html>
<html lang="en">
<head>
<meta charset="utf-8">
<title>Brightwell Gauge Ltd — Envelope Stationery</title>
<link rel="stylesheet" href="https://fonts.googleapis.com/css2?family=Michroma&family=Tinos&display=swap">
<style>
  :root {
    --backdrop: #cfae7c;
    --paper: #ffffff;
    --edge: #3a3a3a;
    --brand-blue: #223a96;
    --name-blue: #2f2aa9;
    --band-grey: #6a6a6c;
    --label-ink: #111111;
  }
  html, body {
    margin: 0;
    padding: 0;
    overflow: hidden;
    background: var(--backdrop);
  }
  .sheet {
    display: block;
    width: 960px;
    height: 1200px;
  }
  .sheet-label {
    font-family: "Tinos", "Times New Roman", serif;
    font-size: 38px;
    fill: var(--label-ink);
  }
  .paper { fill: var(--paper); stroke: var(--edge); stroke-width: 0.8; }
  .flap-open { fill: var(--paper); stroke: var(--edge); stroke-width: 0.8; }
  .flap-closed { fill: var(--brand-blue); }
  .flap-fold { fill: none; stroke: var(--edge); stroke-width: 0.8; }
  .front-band { fill: var(--brand-blue); }
  .brand-name {
    font-family: "Michroma", "Arial", sans-serif;
    font-weight: 400;
    fill: var(--name-blue);
  }
  .front-name { font-size: 72px; }
  .back-band { fill: var(--band-grey); }
  .back-name {
    font-size: 17px;
    letter-spacing: 1px;
    fill: var(--name-blue);
  }
</style>
</head>
<body>
<svg class="sheet" viewBox="0 0 864 1080" xmlns="http://www.w3.org/2000/svg" role="img" aria-label="Brightwell Gauge Ltd envelope, front and back">

  <text class="sheet-label" x="8" y="55">Envelop</text>

  <g class="envelope envelope-front">
    <polygon class="flap-open" points="155,165 180,110 475,53 738,108 770,165"/>
    <rect class="paper" x="152" y="165" width="618" height="287"/>
    <rect class="front-band" x="152" y="390" width="618" height="62"/>
    <text class="brand-name front-name" x="174" y="387" textLength="276" lengthAdjust="spacingAndGlyphs">BGL</text>
  </g>

  <text class="sheet-label" x="155" y="515">Front</text>

  <g class="envelope envelope-back">
    <polygon class="flap-closed" points="138,628 165,573 462,517 724,573 756,628"/>
    <rect class="paper" x="138" y="628" width="618" height="287"/>
    <polyline class="flap-fold" points="138,628 428,690 756,628"/>
    <rect class="back-band" x="138" y="883" width="618" height="32"/>
    <text class="brand-name back-name" x="432" y="905" text-anchor="middle">Brightwell Gauge</text>
  </g>

  <text class="sheet-label" x="156" y="960">Back</text>
</svg>
</body>
</html>
```